New B2C website design to help dads be better dads

DadHarbor is a website to help dads be the “best dad you can be.”

We require our website to be designed into a PSD format, no coding necessary.

The general concept is a two-page design. The first page is the login page, the second page is the home page. Once at the home page, rather than navigating to and from different pages, the user will push and pull through different visual and functional layers of the hierarchy. In theory, this should add to the user experience by having a visual anchor of where they are (through layered pagination) as well as improving loading times since the new information should only be a delta in data load versus a brand new page load.

The general look-and-feel we are going for is clean, simple, minimal. This means that the winning design will show us a good eye for web-optimized typography, good use of white (negative) space, and good use of a visually pleasing grid.

We require a total of 6 page "views" plus the landing page. We note that many of the views are similar to one another.
Landing page
Milestone view
Task view
Content view, articles
Content view, products
Search view
What's new view

Please review all of the additional information provided as well as the attachments for examples.

We provide the following websites as good references for:

Typography:
http://example-kelvorn.com/journal/

Use of white space:
http://www.trenvaskit.com/
http://moldrefin.com/

Example for “scrolling” page concept as well as good balance of color, typography, and white space:
http://www.qorbitalmeet.eu/

Please contact us with questions so that we can guide your design effort.
Updates

Hello designers,

The following information is added to help guide the design process:

1.  For the text dialogue below the landing page, please assume the following word count:
"why are we making dad harbor?": 250 words
"who are we?" 200 words
"what's the deal with the penguin logo?" 300 words

For the social media links, please see http://www.gravelplumbs.com/
Notice the floating "social" bar that is always to the right.  This is the concept we are going for, please try to implement this as you see fit. 

Target Market(s)

Fathers of young children ages 0-6 years old.

Industry/Entity Type

Product

Font styles to use
Sans Serif

Requirements
Must have
• Clean lines, minimal design concept

Incorporation of our logo (see attached document)

Header content is static for all views after landing page, see example

This page WILL be responsive, please keep that in mind when designing
The timeline bar should be to the left, with the timeline bar’s “milestones” also being responsive.

Designer is free to suggest font types, but any fonts used must be royalty-free and web-optimized. We request a minimum number of font types as well as fonts that load relatively fast. We reinforce that visually appealing typography is a significant factor in the winning design choice.

While we are not expecting the winning design to include code, please keep in mind that the final implementation needs to be optimized for desktop, tablet, and mobile platforms.

If you are using stock photography that is not generated by you, please provide where/how we can obtain imagery, as well as price.

All custom graphics must be available in original formats; Photoshop/GIMP layered files for layout design, and vector formats for logos, icons and other graphical elements.

Please incorporate “Blue” into design elements as you see fit, as the RGB 67 74 169 Blue is the primary color used in our brand. The complement to this blue is 255 202 0, a brownish orange. Feel free to use this color as well, although please keep it to a lesser amount.

Background color is your choice, do not feel the need to use the grey.
Should not have
• Excessive graphical content such that it affects loading times

Excessive use of too many font types such that it affects loading times

```html
<!DOCTYPE html>
<html lang="en">
<head>
<meta charset="utf-8">
<title>DadHarbor – Prepare for the baby arrival</title>
<link rel="stylesheet" href="https://fonts.googleapis.com/css2?family=Francois+One&family=Open+Sans:wght@300;400;600;700&family=Poiret+One&family=Raleway:wght@400&display=swap">
<style>
  :root {
    --navy: #1c2b6e;
    --brand-blue: #434aa9;
    --amber: #f0a70d;
    --ink: #1a1a1a;
    --text: #333333;
    --muted: #555555;
    --rule: #d9d9d9;
    --header-top: #ffffff;
    --header-bottom: #dcdcdc;
    --star-on: #f5b82e;
    --star-off: #d4d4d4;
    --page: #ffffff;
  }
  * { box-sizing: border-box; margin: 0; padding: 0; }
  html, body { width: 1200px; height: 956px; overflow: hidden; background: var(--page); }
  body { position: relative; font-family: "Open Sans", Arial, sans-serif; color: var(--text); }

  .site-header {
    position: absolute; left: 0; top: 0; width: 1200px; height: 142px;
    background: linear-gradient(to bottom, var(--header-top), var(--header-bottom));
    border-bottom: 4px solid var(--navy);
  }
  .brand {
    position: absolute; left: 32px; top: 58px; display: flex; align-items: center; gap: 8px;
    font-weight: 700; font-size: 19px; color: var(--navy);
  }
  .brand-mark { width: 16px; height: 16px; border-radius: 50%; background: var(--navy); }
  .welcome {
    position: absolute; left: 192px; top: 14px;
    font-family: "Francois One", Arial, sans-serif; font-size: 38px; color: var(--ink); letter-spacing: 0.3px;
  }
  .dad-score { position: absolute; left: 193px; top: 87px; font-size: 17px; color: var(--ink); }
  .dad-score strong { color: var(--navy); font-weight: 700; }
  .search-field {
    position: absolute; left: 438px; top: 77px; width: 300px; height: 43px;
    background: #fff; border: 1px solid #ccc; border-radius: 4px;
  }
  .btn {
    position: absolute; top: 77px; height: 43px; background: var(--navy); color: #fff;
    border-radius: 4px; font-weight: 700; font-size: 17px; letter-spacing: 0.5px;
    display: flex; align-items: center; justify-content: center;
  }
  .btn-search { left: 748px; width: 114px; }
  .btn-logout { left: 1058px; width: 114px; }
  .account-link { position: absolute; left: 959px; top: 87px; font-size: 17px; color: var(--ink); }

  .milestone-band {
    position: absolute; left: 0; top: 142px; width: 1200px; height: 48px; background: var(--amber);
  }
  .milestone-band h2 {
    position: absolute; left: 56px; top: 7px; font-weight: 400; font-size: 26px; color: var(--ink);
  }
  .band-notch { position: absolute; left: 70px; top: 189px; }

  .task-list {
    position: absolute; left: 56px; top: 232px; width: 263px; height: 289px;
    border: 2px solid var(--rule); border-radius: 6px; list-style: none; padding-top: 17px;
  }
  .task-list li { display: flex; align-items: center; height: 33px; padding-left: 20px; font-size: 17px; color: var(--text); }
  .checkbox {
    width: 19px; height: 19px; border: 1px solid #c8c8c8; border-radius: 3px; margin-right: 15px;
    background: linear-gradient(#fafafa, #e6e6e6); flex: none;
  }
  .checkbox.is-done { background: #dbe6f7; border-color: #8aa6d6; }

  .rating-row { position: absolute; left: 82px; top: 538px; display: flex; align-items: center; font-size: 14px; color: var(--ink); }
  .rating-row span { width: 93px; }
  .comments-label { position: absolute; left: 82px; top: 577px; font-size: 14px; color: var(--ink); }
  .comments-text { position: absolute; left: 82px; top: 602px; width: 232px; font-size: 14.5px; line-height: 21px; color: var(--text); }

  .article-title { position: absolute; left: 349px; top: 224px; font-weight: 300; font-size: 26px; color: var(--ink); }
  .article-rating { position: absolute; left: 878px; top: 229px; display: flex; align-items: center; gap: 14px; }
  .likes { font-size: 15px; color: var(--muted); }
  .likes strong { color: var(--navy); font-weight: 400; }
  .article-body {
    position: absolute; left: 348px; top: 269px; width: 721px; height: 294px;
    border: 1px solid var(--rule); padding: 14px;
  }
  .article-photo {
    position: absolute; left: 14px; top: 14px; width: 243px; height: 145px;
    background: linear-gradient(135deg, #6b5d55 0%, #b89a86 45%, #3e3a3a 100%);
  }
  .article-body p { font-size: 14.8px; line-height: 20.5px; color: var(--text); }
  .article-lead { position: absolute; left: 274px; top: 10px; width: 432px; }
  .article-more { position: absolute; left: 14px; top: 170px; width: 700px; }

  .contact { position: absolute; left: 0; top: 745px; width: 1200px; text-align: center; }
  .contact-kicker { font-weight: 600; font-size: 15px; letter-spacing: 3px; color: var(--muted); }
  .contact-heading { margin-top: 14px; font-family: "Poiret One", Arial, sans-serif; font-size: 46px; color: var(--ink); font-weight: 400; }
  .contact-email { margin-top: 14px; font-weight: 700; font-size: 21px; color: var(--brand-blue); }
  .legal-links { margin-top: 22px; font-family: "Raleway", Arial, sans-serif; font-size: 13.5px; color: var(--muted); }
</style>
</head>
<body>
  <header class="site-header">
    <div class="brand"><span class="brand-mark"></span>DadHarbor</div>
    <h1 class="welcome">Welcome Ravel, what would you like to do today?</h1>
    <div class="dad-score">Super Dad Score: <strong>10,500</strong></div>
    <div class="search-field"></div>
    <div class="btn btn-search">SEARCH</div>
    <div class="account-link">My account</div>
    <div class="btn btn-logout">LOGOUT</div>
  </header>

  <section class="milestone-band"><h2>Prepare for the baby arrival</h2></section>
  <svg class="band-notch" width="44" height="23" viewBox="0 0 44 23"><polygon points="0,0 44,0 22,23" fill="#f0a70d"/></svg>

  <ul class="task-list">
    <li><span class="checkbox"></span>Buy a crib</li>
    <li><span class="checkbox"></span>As semble the crib</li>
    <li><span class="checkbox"></span>Buy a stroller</li>
    <li><span class="checkbox is-done"><svg width="19" height="19" viewBox="0 0 19 19"><path d="M5 10 l3 3 l6 -8" fill="none" stroke="#1c2b6e" stroke-width="2.4" stroke-linecap="round" stroke-linejoin="round"/></svg></span>Buy a carseat</li>
    <li><span class="checkbox"></span>Install a carseat</li>
    <li><span class="checkbox"></span>Learn to change a diaper</li>
    <li><span class="checkbox"></span>Learn to hold a baby</li>
    <li><span class="checkbox"></span>Set a feeding schedule</li>
  </ul>

  <div class="rating-row">
    <span>Rate this :</span>
    <svg width="108" height="21" viewBox="0 0 108 21">
      <defs><polygon id="star" points="10,1 12.6,7.2 19.3,7.6 14.1,11.9 15.8,18.5 10,14.8 4.2,18.5 5.9,11.9 0.7,7.6 7.4,7.2"/></defs>
      <use href="#star" x="0" fill="#f5b82e"/><use href="#star" x="22" fill="#f5b82e"/><use href="#star" x="44" fill="#f5b82e"/><use href="#star" x="66" fill="#d4d4d4"/><use href="#star" x="88" fill="#d4d4d4"/>
    </svg>
  </div>
  <div class="comments-label">Comments:</div>
  <p class="comments-text">Lorem ipsum dolor sit amet, consectetur adipisicing elit, sed do eiusmod tempor incididunt ut labore et dolore magna aliqua. Ut enim ad minim veniam.</p>

  <h3 class="article-title">Just Call Me Dr. Car Seat</h3>
  <div class="article-rating">
    <svg width="108" height="21" viewBox="0 0 108 21">
      <use href="#star" x="0" fill="#f5b82e"/><use href="#star" x="22" fill="#f5b82e"/><use href="#star" x="44" fill="#f5b82e"/><use href="#star" x="66" fill="#d4d4d4"/><use href="#star" x="88" fill="#d4d4d4"/>
    </svg>
    <span class="likes"><strong>3,121</strong> likes</span>
  </div>

  <article class="article-body">
    <div class="article-photo" role="img" aria-label="Photo of a father buckling his baby into a car seat"></div>
    <p class="article-lead">I went out to buy my first car seat and had to earn my PhD in car seats, Newtonian physics, and anti-stain technology. Lorem ipsum dolor sit amet, consectetur adipisicing elit, sed do eiusmod tempor incididunt ut labore et dolore magna aliqua. Ut enim ad minim veniam, quis nostrud exercitation ullamco laboris nisi ut aliquip ex ea commodo consequat.</p>
    <p class="article-more">Lorem ipsum dolor sit amet, consectetur adipisicing elit, sed do eiusmod tempor incididunt ut labore et dolore magna aliqua. Ut enim ad minim veniam, quis nostrud exercitation ullamco laboris nisi ut aliquip ex ea commodo consequat. Duis aute irure dolor in reprehenderit in voluptate velit esse cillum dolore eu fugiat nulla pariatur. Excepteur sint occaecat cupidatat non proident, sunt in culpa qui officia deserunt mollit anim id est laborum.</p>
  </article>

  <footer class="contact">
    <div class="contact-kicker">CONTACT</div>
    <h2 class="contact-heading">GET IN TOUCH</h2>
    <div class="contact-email">info@dadharbor.com</div>
    <div class="legal-links">Privacy Policy &nbsp;|&nbsp; © 2013 DadHarbor &nbsp;|&nbsp; Terms Policy &nbsp;|&nbsp; Disclaimer</div>
  </footer>
</body>
</html>
```